Kestrada LLC, needs a web page no more than 5 pages (for now)

Kestrada is a general contractor. Our services include general contracting, design-build construction, disaster recovery and environmental remediation. Our main clients are PMX, TQ, State and Local Gov't Agencies, Hospitals and Schools. Kestrada is also a SDVOSB.

```html
<!DOCTYPE html>
<html lang="en">
<head>
<meta charset="utf-8">
<title>Kestrada LLC — General Contracting</title>
<link href="https://fonts.googleapis.com/css2?family=Montserrat:ital,wght@0,500;0,600;0,700;1,700&family=Lato:wght@400;700&display=swap" rel="stylesheet">
<style>
:root{
  --gold:#c9943f;
  --gold-deep:#d7962e;
  --gold-light:#e9b35a;
  --ink:#1b1b1b;
  --text:#3c3c3c;
  --muted:#5a5a5a;
  --cream:#f8ece0;
  --white:#ffffff;
  --footer:#1f1f1f;
  --line:#d9c7b2;
}
*{margin:0;padding:0;box-sizing:border-box}
html,body{width:1200px;height:3701px;overflow:hidden}
body{font-family:'Lato',sans-serif;color:var(--text);background:var(--white);position:relative}
.abs{position:absolute}
.heading{font-family:'Montserrat',sans-serif;font-weight:600;color:var(--ink)}
.btn{position:absolute;display:flex;align-items:center;justify-content:center;border-radius:30px;background:var(--gold);color:var(--white);font-family:'Lato',sans-serif;font-weight:700;font-size:17px;text-decoration:none}

/* header */
.site-header{position:absolute;left:0;top:0;width:1200px;height:93px;background:var(--white)}
.brand{position:absolute;display:flex;align-items:center;gap:8px;font-family:'Montserrat',sans-serif;font-weight:600;color:var(--gold)}
.brand-dot{width:14px;height:14px;border-radius:50%;background:var(--gold)}
.nav{position:absolute;left:470px;top:32px;display:flex;gap:25px;font-size:15.5px;color:var(--ink)}
.nav .active{color:var(--gold);text-decoration:underline}

/* hero */
.hero{position:absolute;left:0;top:93px;width:1200px;height:570px;background:linear-gradient(100deg,#3a2a1c 0%,#6b5034 45%,#9c7e5b 70%,#4b3a2a 100%)}
.hero-title{position:absolute;left:112px;top:105px;font-family:'Montserrat',sans-serif;font-weight:700;font-size:53px;line-height:61px;color:var(--white)}
.hero-title em{font-style:italic}

/* about */
.about-image{position:absolute;left:131px;top:744px;width:408px;height:408px;border-radius:50%;border:6px solid var(--gold);background:radial-gradient(circle,#9fc7ef 0%,#3e7fc6 60%,#1d4f8f 100%)}
.about-copy{position:absolute;left:641px;top:741px;width:445px}
.about-copy h2{font-size:40px;margin-bottom:20px}
.about-copy p{font-size:14.5px;line-height:25.8px;text-align:justify}

/* services */
.services{position:absolute;left:0;top:1237px;width:1200px;height:717px;background:var(--cream)}
.services-intro{position:absolute;left:107px;top:100px;width:385px}
.services-intro h2{font-size:40px;margin-bottom:24px}
.services-intro p{font-size:15.5px;line-height:30px;margin-bottom:16px}
.card{position:absolute;width:281px;height:256px;border:1px solid var(--line);border-radius:10px;background:var(--white);padding:28px 20px}
.card.featured{background:linear-gradient(160deg,var(--gold-deep),var(--gold-light));border-color:transparent;color:var(--white)}
.card h3{font-family:'Montserrat',sans-serif;font-weight:500;font-size:19.5px;margin:20px 0 14px;color:var(--ink);line-height:26px}
.card.featured h3,.card.featured p{color:var(--white)}
.card p{font-size:14px;line-height:22px;color:var(--muted)}
.card svg{width:60px;height:60px}

/* why */
.why h2{position:absolute;left:107px;top:2030px;font-size:40px}
.why-list{position:absolute;left:112px;top:2105px;width:440px;list-style:none}
.why-list li{position:relative;padding-left:36px;font-size:14px;line-height:27px;margin-bottom:12px;color:var(--muted)}
.why-list li strong{font-weight:400;color:var(--ink);font-size:16px}
.why-list li svg{position:absolute;left:0;top:6px}
.why-shadow{position:absolute;left:651px;top:2049px;width:447px;height:368px;background:var(--gold)}
.why-image{position:absolute;left:642px;top:2040px;width:447px;height:368px;background:linear-gradient(135deg,#0f2c4f 0%,#1c5a8f 50%,#c46a1e 85%,#2a2a2a 100%)}

/* cta */
.cta{position:absolute;left:0;top:2467px;width:1200px;height:355px;background:var(--gold-deep);text-align:center;color:var(--white)}
.cta h2{color:var(--white);font-size:41px;margin-top:75px}
.cta p{font-size:15px;line-height:26px;margin-top:22px}

/* testimonials */
.testi-title{position:absolute;left:0;top:2895px;width:1200px;text-align:center;font-size:40px}
.testi{position:absolute;top:2995px;width:310px;height:255px;background:var(--white);border-radius:12px;box-shadow:0 3px 10px rgba(0,0,0,.12);padding:40px 24px}
.testi .quote{position:absolute;left:22px;top:-28px;font-family:'Montserrat',sans-serif;font-weight:700;font-size:70px;color:#e4bf86;line-height:1}
.testi p{font-size:14.5px;line-height:26.5px;color:var(--text)}
.person{position:absolute;left:24px;top:175px;display:flex;align-items:center;gap:18px}
.avatar{width:72px;height:72px;border-radius:50%;background:linear-gradient(160deg,#e2ddd8,#b9b2aa)}
.person b{display:block;font-weight:400;font-size:19px;color:var(--ink)}
.person span{font-size:14.5px;color:var(--muted)}
.arrow{position:absolute;top:3081px;width:30px;height:30px;border-radius:50%;display:flex;align-items:center;justify-content:center}

/* footer */
.site-footer{position:absolute;left:0;top:3335px;width:1200px;height:366px;background:var(--footer);color:var(--white)}
.site-footer h4{font-family:'Lato',sans-serif;font-weight:400;font-size:19px;margin-bottom:18px}
.quick{position:absolute;left:219px;top:82px}
.quick ul{list-style:none}
.quick li{font-size:15px;margin-bottom:15px;padding-left:22px;position:relative}
.quick li::before{content:"";position:absolute;left:0;top:5px;width:8px;height:8px;background:var(--white)}
.contact{position:absolute;left:887px;top:82px}
.contact .row{display:flex;gap:16px;font-size:16px;line-height:25px;margin-bottom:12px}
.contact svg{flex:none;margin-top:3px}
.socials{position:absolute;left:551px;top:247px;display:flex;gap:12px}
.socials span{width:20px;height:20px;border-radius:50%;background:var(--white)}
.footer-rule{position:absolute;left:110px;top:322px;width:980px;height:1px;background:#555}
.copy{position:absolute;left:0;top:338px;width:1200px;text-align:center;font-size:14.5px}
</style>
</head>
<body>

<header class="site-header">
  <div class="brand" style="left:112px;top:32px;font-size:26px"><span class="brand-dot"></span>Kestrada</div>
  <nav class="nav">
    <span class="active">Home</span><span>About</span><span>Services</span><span>Clients &amp; Markets</span><span>Testimonials</span>
  </nav>
  <a class="btn" style="left:946px;top:20px;width:142px;height:48px;font-weight:400;font-size:16px">Contact Us</a>
</header>

<section class="hero" role="img" aria-label="Construction supervisor in a hard hat reviewing blueprints at a timber-frame building site">
  <h1 class="hero-title">SDVOSB-Certified<br><em>Mission-Focused</em><br>Results-Driven</h1>
  <a class="btn" style="left:108px;top:319px;width:153px;height:48px;font-weight:400">Get Started</a>
</section>

<section class="about">
  <div class="about-image" role="img" aria-label="Blue holographic architectural model of a house over plans"></div>
  <div class="about-copy">
    <h2 class="heading">About Us</h2>
    <p>Kestrada is a mission-driven general contracting firm specializing in construction services for government agencies, healthcare institutions, and educational facilities. As a Service-Disabled Veteran-Owned Small Business (SDVOSB), we bring a unique blend of leadership, discipline, and accountability to every project we undertake. We don’t just build — we solve problems, deliver results, and support the infrastructure that serves our communities and our country.</p>
  </div>
  <a class="btn" style="left:641px;top:1035px;width:146px;height:46px">Read More</a>
</section>

<section class="services">
  <div class="services-intro">
    <h2 class="heading">Our Services</h2>
    <p>At Kestrada, we deliver <b style="color:var(--ink)">mission-ready construction solutions</b> with the expertise and reliability trusted by government agencies, healthcare systems, and educational institutions. Our core services include:</p>
    <p>From large-scale government projects to critical hospital and school infrastructure, we provide the strength, reliability, and innovation needed to meet complex challenges.</p>
    <p>We provide the strength, reliability, and innovation needed to meet complex challenges.</p>
  </div>
  <a class="btn" style="left:107px;top:555px;width:262px;height:48px">Explore Our Services</a>

  <div class="card featured" style="left:509px;top:84px">
    <svg viewBox="0 0 60 60" fill="none" stroke="#fff" stroke-width="2"><rect x="8" y="6" width="34" height="44" rx="3"/><path d="M15 16h20M15 24h20M15 32h12"/><path d="M30 44l8-6 8 6 8-4"/></svg>
    <h3>General Contracting</h3>
    <p>Full-service project management from planning to completion, ensuring quality, efficiency, and</p>
  </div>
  <div class="card" style="left:808px;top:84px">
    <svg viewBox="0 0 60 60" fill="none" stroke="#d7962e" stroke-width="2"><rect x="6" y="8" width="32" height="42" rx="3"/><path d="M16 8V4h12v4"/><circle cx="40" cy="36" r="9"/><path d="M47 43l8 8"/></svg>
    <h3>Design-Build</h3>
    <p>Streamlined, efficient, and cost-effective construction delivery.Streamlined, efficient, and</p>
  </div>
  <div class="card" style="left:509px;top:373px">
    <svg viewBox="0 0 60 60" fill="none" stroke="#d7962e" stroke-width="2"><circle cx="30" cy="30" r="12"/><circle cx="30" cy="30" r="22" stroke-dasharray="6 4"/></svg>
    <h3>Disaster Recovery</h3>
    <p>Rapid deployment teams ready to restore facilities and infrastructure after natural disasters, ensuring</p>
  </div>
  <div class="card" style="left:808px;top:373px">
    <svg viewBox="0 0 60 60" fill="none" stroke="#d7962e" stroke-width="2"><circle cx="30" cy="30" r="22"/><path d="M22 38c0-12 8-18 18-18 0 10-6 18-18 18zM22 38l10-10"/></svg>
    <h3>Environmental Remediation</h3>
    <p>Safe, compliant, and sustainable cleanup and restoration services</p>
  </div>
</section>

<section class="why">
  <h2 class="heading">Why Choose Us?</h2>
  <ul class="why-list">
    <li><svg width="22" height="16" viewBox="0 0 22 16" fill="none" stroke="#d7962e" stroke-width="3"><path d="M2 2l6 6-6 6M11 2l6 6-6 6"/></svg><strong>SDVOSB Certified</strong> – As a Service-Disabled Veteran-Owned Small Business (SDVOSB), we understand</li>
    <li><svg width="22" height="16" viewBox="0 0 22 16" fill="none" stroke="#d7962e" stroke-width="3"><path d="M2 2l6 6-6 6M11 2l6 6-6 6"/></svg><strong>Proven Government Contractor</strong> – The PMX Agency (PMX)&nbsp; the TQ Administration (TQ)</li>
    <li><svg width="22" height="16" viewBox="0 0 22 16" fill="none" stroke="#d7962e" stroke-width="3"><path d="M2 2l6 6-6 6M11 2l6 6-6 6"/></svg><strong>Comprehensive Services</strong> – From design-build to disaster recovery, general contracting, and environmental</li>
    <li><svg width="22" height="16" viewBox="0 0 22 16" fill="none" stroke="#d7962e" stroke-width="3"><path d="M2 2l6 6-6 6M11 2l6 6-6 6"/></svg><strong>Mission-Focused Construction</strong> – Our roots in military service shape how we approach every project — with</li>
    <li><svg width="22" height="16" viewBox="0 0 22 16" fill="none" stroke="#d7962e" stroke-width="3"><path d="M2 2l6 6-6 6M11 2l6 6-6 6"/></svg><strong>Safety &amp; Compliance First</strong> – We prioritize safety, environmental stewardship, and regulatory compliance in</li>
  </ul>
  <div class="why-shadow"></div>
  <div class="why-image" role="img" aria-label="Engineer in hard hat and safety vest using a tablet with digital building overlays"></div>
</section>

<section class="cta">
  <h2 class="heading">Let’s Build Something That Lasts</h2>
  <p>Discover expert 3D printing and engraving services. We turn your visions into reality,<br>supporting veterans along the way!</p>
  <a class="btn" style="left:527px;top:223px;width:146px;height:47px;background:var(--white);color:var(--ink);font-weight:400">Contact Us</a>
</section>

<section class="testimonials">
  <h2 class="heading testi-title">What Our Clients Say</h2>
  <div class="arrow" style="left:42px;background:var(--gold-deep)"><svg width="12" height="14" viewBox="0 0 12 14" fill="none" stroke="#fff" stroke-width="2.5"><path d="M8 2L3 7l5 5"/></svg></div>
  <div class="arrow" style="left:1129px;background:#8a8a8a"><svg width="12" height="14" viewBox="0 0 12 14" fill="none" stroke="#fff" stroke-width="2.5"><path d="M4 2l5 5-5 5"/></svg></div>

  <div class="testi" style="left:111px">
    <span class="quote">“</span>
    <p>Kestrada delivered our project ahead of schedule and with zero safety incidents. Their attention to detail and professionalism made them stand out</p>
    <div class="person"><div class="avatar" role="img" aria-label="Client portrait"></div><div><b>Renata Olsson</b><span>Facilities Manager</span></div></div>
  </div>
  <div class="testi" style="left:446px">
    <span class="quote">“</span>
    <p>From design to completion, Kestrada exceeded expectations. Their team communicated clearly, adapted to unexpected challenges, and ensured</p>
    <div class="person"><div class="avatar" role="img" aria-label="Client portrait"></div><div><b>Daniel Okafor</b><span>Project Officer</span></div></div>
  </div>
  <div class="testi" style="left:781px">
    <span class="quote">“</span>
    <p>Kestrada played a critical role in our disaster recovery efforts. Their rapid response and structured process helped us reopen our facility in record</p>
    <div class="person"><div class="avatar" role="img" aria-label="Client portrait"></div><div><b>Priya Castell</b><span>Emergency Manager,</span></div></div>
  </div>
</section>

<footer class="site-footer">
  <div class="quick">
    <h4>Quick Links</h4>
    <ul><li>Home</li><li>About</li><li>Services</li><li>Clients &amp; Markets</li><li>Testimonials</li></ul>
  </div>
  <div class="brand" style="left:0;top:135px;width:1200px;justify-content:center;font-size:38px"><span class="brand-dot" style="width:18px;height:18px"></span>Kestrada</div>
  <div class="socials"><span></span><span></span><span></span></div>
  <div class="contact">
    <h4>Contact Us</h4>
    <div class="row"><svg width="20" height="20" viewBox="0 0 20 20"><circle cx="10" cy="10" r="10" fill="#fff"/><path d="M6 5l2 0 1 3-1.5 1a7 7 0 003.5 3.5l1-1.5 3 1v2a1 1 0 01-1 1A9 9 0 015 6a1 1 0 011-1z" fill="#1f1f1f"/></svg>+1 555 014 2290</div>
    <div class="row"><svg width="20" height="20" viewBox="0 0 20 20"><circle cx="10" cy="10" r="10" fill="#fff"/><rect x="5" y="6.5" width="10" height="7" fill="none" stroke="#1f1f1f" stroke-width="1.5"/><path d="M5 7l5 4 5-4" fill="none" stroke="#1f1f1f" stroke-width="1.5"/></svg>info@kestrada.com</div>
    <div class="row"><svg width="20" height="20" viewBox="0 0 20 20"><path d="M10 1a7 7 0 00-7 7c0 5 7 11 7 11s7-6 7-11a7 7 0 00-7-7z" fill="#fff"/><circle cx="10" cy="8" r="2.5" fill="#1f1f1f"/></svg>48 Harbor Lane, Brookfield,<br>ST 00000</div>
  </div>
  <div class="footer-rule"></div>
  <p class="copy">© 2025 Kestrada All rights reserved.</p>
</footer>

</body>
</html>
```